Refresh Application User Interface

Brightmoor wishes to update the look of its business applications. Two representative forms are shown below. Please note, we are not considering changes in functionality or usability. Our goal is a cleaner, more contemporary design.

Industry/Entity Type

Business

```html
<!DOCTYPE html>
<html lang="en">
<head>
<meta charset="utf-8">
<title>Brightmoor – Purchase Order Lines</title>
<link href="https://fonts.googleapis.com/css2?family=Open+Sans:wght@400;600;700;800&family=Arimo:ital,wght@0,400;1,400&display=swap" rel="stylesheet">
<style>
:root{
  --ink:#222;
  --muted:#444;
  --topbar:#141414;
  --tab:#e4e6e8;
  --blue:#2196ee;
  --blue-dark:#1a6fc0;
  --pill-dark:#1f73c9;
  --toolbar:#4b5b66;
  --panel-line:#d5d9dc;
  --grid-bar:#cfdcea;
  --row:#f4f4f4;
  --link:#1a3fbf;
  --field-blue:#1d2fb0;
  --green:#1a8a1a;
  --red:#e01010;
  --note:#fff8b0;
  --status:#fffdea;
}
*{box-sizing:border-box;margin:0;padding:0}
html,body{width:1200px;height:897px;overflow:hidden;background:#fff}
.app{position:relative;width:1086px;height:812px;transform:scale(1.105);transform-origin:0 0;font-family:"Open Sans",sans-serif;color:var(--ink)}
.abs{position:absolute}
.topbar{left:0;top:0;width:1086px;height:28px;background:var(--topbar);color:#fff;font-size:13px}
.topbar .user{left:19px;top:5px}
.topbar .user b,.topbar .role b{font-weight:700}
.topbar .role{left:212px;top:5px}
.topbar .links{right:0;top:0;display:flex;height:28px}
.topbar .links span{padding:5px 8px;border-left:1px solid #3a3a3a}
.modules{left:20px;top:38px;display:flex;gap:2px}
.modules span{background:var(--tab);padding:6px 11px;font-size:14px;font-weight:600;color:#444;height:32px}
.modules .on{background:var(--blue);color:#fff}
.brand{right:20px;top:30px;font-size:31px;font-weight:800;color:var(--blue-dark);letter-spacing:1px}
.nav{left:0;top:70px;width:1086px;height:29px;background:var(--blue);display:flex;align-items:center;padding-left:20px;gap:4px}
.nav span{color:#fff;font-size:13px;font-weight:600;padding:2px 7px;border-radius:10px}
.nav .on{background:#fff;color:var(--blue-dark)}
.nav .hl{background:var(--pill-dark)}
.nav .gap{margin-left:12px}
.title{left:18px;top:108px;font-size:22px;color:var(--muted);font-weight:400}
.subtabs{right:20px;top:110px;display:flex;gap:2px}
.subtabs span{background:#eef0f1;font-size:14px;color:#444;padding:4px 9px;height:29px;position:relative}
.subtabs .on{background:var(--toolbar);color:#fff}
.subtabs .dot{position:absolute;right:-2px;top:-1px;width:9px;height:9px;border-radius:50%;background:#4cbb4c}
.toolbar{left:20px;top:139px;width:1046px;height:29px;background:var(--toolbar);color:#fff;font-size:13px}
.toolbar .item{top:0;height:29px;display:flex;align-items:center;gap:5px}
.toolbar .dim{color:#9aa5ad}
.panel{left:20px;top:168px;width:1046px;height:620px;border:1px solid var(--panel-line);border-top:none}
.head{left:32px;top:180px;width:1022px;height:83px;background:#f7f7f7;border:1px solid #e2e2e2;font-family:Arimo,sans-serif;font-size:13px}
.head .vendor{left:215px;top:46px;width:360px;height:21px;background:#e9e9e9;padding:2px 3px}
.grid{left:32px;top:274px;width:1022px;height:465px;border:1px solid #c8d0d8;background:#f1f1f1}
.gridbar{left:0;top:0;width:1020px;height:25px;background:var(--grid-bar)}
.pager{right:0;top:0;display:flex;height:25px;font-size:13px;color:#333}
.pager span{padding:3px 9px;border-left:1px solid #b8c6d6}
.cols{top:30px;font-size:13px;font-weight:600;color:#333}
.row{left:0;width:1020px;font-family:Arimo,sans-serif;font-size:13px}
.r1{top:53px;height:82px;background:var(--row)}
.r2{top:136px;height:82px;background:var(--row)}
.r3{top:219px;height:83px;background:var(--row)}
.fld{position:absolute;height:21px;border:1px solid #8a8a8a;background:#fff;padding:2px 3px;white-space:nowrap;overflow:hidden}
.sel::after{content:"";position:absolute;right:0;top:0;width:18px;height:19px;border-left:1px solid #8a8a8a;background:#f3f3f3}
.sel svg{position:absolute;right:4px;top:6px;z-index:1}
.chk{position:absolute;width:14px;height:14px;border:1px solid #777;background:#fff}
.link{color:var(--link);text-decoration:underline}
.blue{color:var(--field-blue)}
.ital{font-style:italic}
.red{color:var(--red)}
.note{position:absolute;width:17px;height:17px;background:var(--note);border:1px solid #b8a800;background:#f7ee3a}
.cal{position:absolute;width:18px;height:18px;border:1px solid #8a2a2a;background:#fff}
.status{left:32px;top:749px;width:1022px;height:26px;background:var(--status);border:1px dashed #e6deaa;text-align:center;font-size:14px;color:#333;padding-top:3px}
</style>
</head>
<body>
<div class="app">
  <div class="abs topbar">
    <div class="abs user">Logged In As <b>Dana Whitlock</b> <svg width="12" height="12" viewBox="0 0 12 12"><circle cx="6" cy="6" r="4" fill="none" stroke="#aaa" stroke-width="2.5"/></svg></div>
    <div class="abs role">Current Role <b>administrator</b> <svg width="10" height="8"><path d="M1 2l4 4 4-4" stroke="#aaa" stroke-width="2" fill="none"/></svg></div>
    <div class="abs links"><span>Touch</span><span>New Tab</span><span>Help</span><span>Support</span><span>Log Out</span></div>
  </div>

  <div class="abs modules"><span>Home</span><span>eSource</span><span class="on">eBuy</span><span>eRequest</span><span>eSell</span><span>eStock</span><span>ePlan</span><span>Preferences</span></div>
  <div class="abs brand">BRIGHTMOOR</div>

  <div class="abs nav"><span class="on">Orders</span><span>Receipes</span><span>Shipments</span><span>Invoices</span><span class="gap">Pricing</span><span class="hl">Tables</span><span>Reports</span><span>Inquiries</span><span>Periodic Tasks</span><span>Workflows</span></div>

  <h1 class="abs title">Purchase Order Lines</h1>
  <div class="abs subtabs"><span>Header</span><span class="on">Lines<i class="dot"></i></span><span>Charges</span><span>Notes<i class="dot"></i></span></div>

  <div class="abs toolbar">
    <div class="abs item" style="left:8px"><svg width="18" height="18" viewBox="0 0 18 18"><path d="M5 12l7-7a2 2 0 013 3l-8 8a3 3 0 01-4-4l7-7" stroke="#fff" stroke-width="1.8" fill="none"/></svg></div>
    <div class="abs item" style="left:42px"><svg width="18" height="18"><rect x="2" y="1" width="11" height="15" fill="none" stroke="#fff" stroke-width="1.5"/><circle cx="10" cy="10" r="3.5" stroke="#fff" stroke-width="1.5" fill="none"/><path d="M12.5 12.5l4 4" stroke="#fff" stroke-width="2"/></svg></div>
    <div class="abs item" style="left:75px"><svg width="22" height="18"><circle cx="4" cy="12" r="3" fill="#fff"/><circle cx="11" cy="6" r="3" fill="#fff"/><circle cx="18" cy="12" r="3" fill="#fff"/></svg></div>
    <div class="abs item" style="left:112px"><svg width="20" height="18"><rect x="1" y="5" width="18" height="11" rx="1" fill="#fff"/><rect x="7" y="2" width="6" height="4" fill="none" stroke="#fff" stroke-width="1.5"/></svg></div>
    <div class="abs item" style="left:148px"><svg width="18" height="18"><circle cx="9" cy="9" r="8" fill="#6d7b85"/><text x="9" y="13" text-anchor="middle" font-size="11" fill="#4b5b66" font-weight="700">?</text></svg></div>
    <div class="abs item" style="left:182px"><svg width="20" height="20"><path d="M3 17l10-10M13 3l4 4M3 3l14 14" stroke="#fff" stroke-width="2.2"/></svg>View GL Accounts</div>
    <div class="abs item" style="left:337px"><svg width="20" height="20"><rect x="1" y="2" width="13" height="14" fill="#fff"/><circle cx="15" cy="15" r="4.5" fill="#4cbb4c"/></svg>Post Order</div>
    <div class="abs item dim" style="left:700px"><svg width="13" height="13"><circle cx="5" cy="5" r="4" stroke="#9aa5ad" stroke-width="1.5" fill="none"/><path d="M8 8l4 4" stroke="#9aa5ad" stroke-width="1.5"/></svg>search</div>
    <div class="abs item dim" style="left:778px"><svg width="12" height="12"><circle cx="6" cy="6" r="6" fill="#6b8a6b"/></svg>new</div>
    <div class="abs item" style="left:832px;background:#3d4b55;padding:0 10px"><svg width="13" height="11"><path d="M1 6l4 4 7-9" stroke="#7ed957" stroke-width="2.2" fill="none"/></svg>apply</div>
    <div class="abs item" style="left:913px"><svg width="13" height="13"><circle cx="6.5" cy="6.5" r="6.5" fill="#e8412c"/><path d="M4 4l5 5M9 4l-5 5" stroke="#fff" stroke-width="1.6"/></svg>delete</div>
    <div class="abs item" style="left:989px"><svg width="14" height="12"><path d="M5 1L1 5l4 4M1 5h8a4 4 0 014 4v2" stroke="#fff" stroke-width="1.8" fill="none"/></svg>back</div>
  </div>

  <div class="abs panel"></div>

  <div class="abs head">
    <div class="abs" style="left:45px;top:14px">Order #&nbsp;&nbsp; 100159</div>
    <div class="abs" style="left:217px;top:13px;font-size:15px;color:var(--green)">Regular Purchase Order</div>
    <div class="abs" style="left:816px;top:13px;font-size:15px;color:#1a2fe0">Hold For Completion</div>
    <div class="abs vendor">Harbor Clinical Goods, Eastport MA</div>
  </div>

  <div class="abs grid">
    <div class="abs gridbar">
      <svg class="abs" style="left:8px;top:5px" width="14" height="15"><path d="M12 2H2l6 6-6 6h10" stroke="#222" stroke-width="2" fill="none"/></svg>
      <svg class="abs" style="left:38px;top:5px" width="15" height="15"><rect x="1" y="4" width="9" height="10" fill="#fff" stroke="#222" stroke-width="1.5"/><rect x="5" y="1" width="9" height="10" fill="#fff" stroke="#222" stroke-width="1.5"/></svg>
      <div class="abs" style="left:62px;top:0;width:31px;height:25px;background:#b8c9dc"></div>
      <svg class="abs" style="left:70px;top:5px" width="15" height="16"><rect x="1" y="3" width="11" height="12" fill="none" stroke="#222" stroke-width="1.5"/><rect x="4" y="1" width="5" height="4" fill="#222"/></svg>
      <svg class="abs" style="left:100px;top:5px" width="16" height="15"><path d="M1 3h14M1 8h14M1 13h14" stroke="#222" stroke-width="1.5"/><circle cx="10" cy="3" r="2" fill="#fff" stroke="#222"/><circle cx="5" cy="8" r="2" fill="#fff" stroke="#222"/><circle cx="11" cy="13" r="2" fill="#fff" stroke="#222"/></svg>
      <svg class="abs" style="left:131px;top:5px" width="15" height="15"><circle cx="7.5" cy="7.5" r="7" fill="#e8412c"/><path d="M5 5l5 5M10 5l-5 5" stroke="#fff" stroke-width="1.6"/></svg>
      <div class="abs pager"><span>I&#9664;</span><span style="background:#b8c9dc;color:#fff">&#10218;</span><span>Page 1 of 1</span><span>&#10219;</span><span>&#9654;I</span></div>
    </div>

    <div class="abs cols" style="left:5px">Line #</div>
    <div class="abs cols" style="left:78px">Product</div>
    <div class="abs cols" style="left:203px">Supplier Part#</div>
    <div class="abs cols" style="left:346px">Open Qty</div>
    <div class="abs cols" style="left:444px">Unit</div>
    <div class="abs cols" style="left:550px">Unit Price</div>
    <div class="abs cols" style="left:669px">Extended</div>
    <div class="abs cols" style="left:799px">LI Type / Ship To</div>
    <span class="chk" style="left:995px;top:32px"></span>

    <div class="abs row r1">
      <div class="abs link" style="left:11px;top:8px">10</div>
      <div class="fld" style="left:78px;top:4px;width:130px">P-1200</div>
      <svg class="abs" style="left:213px;top:7px" width="14" height="15"><circle cx="8" cy="6" r="4.5" stroke="#2a64b0" stroke-width="2" fill="none"/><path d="M5 9l-4 5" stroke="#2a64b0" stroke-width="2"/></svg>
      <span class="chk" style="left:246px;top:8px"></span>
      <div class="fld" style="left:341px;top:4px;width:88px">1</div>
      <div class="fld sel" style="left:440px;top:4px;width:78px">Ea<svg width="10" height="7"><path d="M1 1l4 4 4-4" stroke="#222" stroke-width="2" fill="none"/></svg></div>
      <div class="fld" style="left:540px;top:4px;width:109px">$6.50</div>
      <div class="abs blue" style="left:666px;top:7px">$6.50</div>
      <div class="fld sel" style="left:787px;top:4px;width:178px">Receive&amp;Pay<svg width="10" height="7"><path d="M1 1l4 4 4-4" stroke="#222" stroke-width="2" fill="none"/></svg></div>
      <span class="chk" style="left:995px;top:10px"></span>
      <div class="fld blue" style="left:78px;top:27px;width:571px">Millbrook 389317 - Brochure Paper, Ultra Smooth Text, 8 1/2" x 11", 28 lb., 96 Brightness</div>
      <div class="abs blue ital" style="left:666px;top:30px">ALCH</div>
      <div class="fld sel" style="left:787px;top:27px;width:178px"><svg width="10" height="7"><path d="M1 1l4 4 4-4" stroke="#222" stroke-width="2" fill="none"/></svg></div>
      <div class="abs" style="left:120px;top:54px">On Purchase Orders</div>
      <div class="abs link" style="left:245px;top:54px">30</div>
      <div class="abs" style="left:343px;top:54px">Available&nbsp;&nbsp;0</div>
      <div class="abs red ital" style="left:540px;top:53px;text-decoration:underline">Over Budget</div>
      <div class="abs red" style="left:666px;top:53px">Pending</div>
      <span class="note" style="left:798px;top:54px"></span>
      <span class="cal" style="left:867px;top:54px"></span>
    </div>

    <div class="abs row r2">
      <div class="abs link" style="left:11px;top:8px">20</div>
      <div class="fld" style="left:78px;top:4px;width:130px">P-1100</div>
      <svg class="abs" style="left:213px;top:7px" width="14" height="15"><circle cx="8" cy="6" r="4.5" stroke="#2a64b0" stroke-width="2" fill="none"/><path d="M5 9l-4 5" stroke="#2a64b0" stroke-width="2"/></svg>
      <span class="chk" style="left:246px;top:8px"></span>
      <div class="fld" style="left:341px;top:4px;width:88px">1</div>
      <div class="fld sel" style="left:440px;top:4px;width:78px">Ea<svg width="10" height="7"><path d="M1 1l4 4 4-4" stroke="#222" stroke-width="2" fill="none"/></svg></div>
      <div class="fld" style="left:540px;top:4px;width:109px">$5.00</div>
      <div class="abs blue" style="left:666px;top:7px">$5.00</div>
      <div class="fld sel" style="left:787px;top:4px;width:178px">Receive&amp;Pay<svg width="10" height="7"><path d="M1 1l4 4 4-4" stroke="#222" stroke-width="2" fill="none"/></svg></div>
      <span class="chk" style="left:995px;top:10px"></span>
      <div class="fld blue" style="left:78px;top:27px;width:571px">Snowcrest 454230 - Recycled Laser Paper 1 case(2,500 count)&nbsp; - 24lb,&nbsp; 90 bright</div>
      <div class="abs blue ital" style="left:666px;top:30px">ALCH</div>
      <div class="fld sel" style="left:787px;top:27px;width:178px"><svg width="10" height="7"><path d="M1 1l4 4 4-4" stroke="#222" stroke-width="2" fill="none"/></svg></div>
      <div class="abs" style="left:120px;top:54px">On Purchase Orders</div>
      <div class="abs link" style="left:245px;top:54px">170</div>
      <div class="abs" style="left:343px;top:54px">Available&nbsp;&nbsp;0</div>
      <div class="abs red ital" style="left:540px;top:53px;text-decoration:underline">Over Budget</div>
      <div class="abs red" style="left:666px;top:53px">Pending</div>
      <span class="note" style="left:798px;top:54px"></span>
      <span class="cal" style="left:867px;top:54px"></span>
    </div>

    <div class="abs row r3">
      <div class="fld" style="left:8px;top:4px;width:59px"></div>
      <div class="fld" style="left:78px;top:4px;width:130px"></div>
      <svg class="abs" style="left:213px;top:7px" width="14" height="15"><circle cx="8" cy="6" r="4.5" stroke="#2a64b0" stroke-width="2" fill="none"/><path d="M5 9l-4 5" stroke="#2a64b0" stroke-width="2"/></svg>
      <span class="chk" style="left:246px;top:8px"></span>
      <div class="fld" style="left:341px;top:4px;width:88px"></div>
      <div class="fld sel" style="left:440px;top:4px;width:78px"><svg width="10" height="7"><path d="M1 1l4 4 4-4" stroke="#222" stroke-width="2" fill="none"/></svg></div>
      <div class="fld" style="left:540px;top:4px;width:109px"></div>
      <div class="fld sel" style="left:787px;top:4px;width:178px">Receive&amp;Pay<svg width="10" height="7"><path d="M1 1l4 4 4-4" stroke="#222" stroke-width="2" fill="none"/></svg></div>
      <div class="fld" style="left:78px;top:27px;width:571px"></div>
      <div class="fld sel" style="left:787px;top:27px;width:178px"><svg width="10" height="7"><path d="M1 1l4 4 4-4" stroke="#222" stroke-width="2" fill="none"/></svg></div>
    </div>
  </div>

  <div class="abs status">Click Search, or enter property values and click Apply</div>
</div>
</body>
</html>
```